Calden L - Premium Business Cards

Background of Calden L
Calden Leafworks is a cigar mobile lounge where guests become family. A place of luxury, relaxation, and ambiance is the global popularity demand. Calden Leafworks strives to provide first-class service of quality and products. Our goal is to ensure that every guest is treated and serviced as a VIP.

Calden Leafworks was founded by Dennis Markow Jr in January 2020. After 15 years of cigar reviews and research Dennis decided it was time to launch his own cigar brand and boutique cigar company. With a wealth of knowledge and years of experience Calden Leafworks was born. With opulence for all cultures, Calden Leafworks offers hand rolled cigars with premium blend tobacco from sweet to bold imported from Costa Rica, Dominican Republic, and Nicaragua. Thank you for your business!

Objective:
Create a business card template to be used for all employees. Design should communicate premium and classy. And should use earth tone colors.

Design should include:
1. Client wants to incorporate the cigar leaf
2. Logo
3. Tagline: Savor every leaf
3. Content info:
Kevin Oldacre
Owner
555-017-4863
koldacre@caldenleaf.com
caldenleafworks.com

```html
<!DOCTYPE html>
<html lang="en">
<head>
<meta charset="utf-8">
<title>Calden Leafworks – Business Cards</title>
<link href="https://fonts.googleapis.com/css2?family=Open+Sans:wght@400;700&display=swap" rel="stylesheet">
<style>
  :root {
    --stage: #3a3a3a;
    --card: #111111;
    --card-back: #141414;
    --ink: #ffffff;
    --ink-soft: #d9d9d9;
    --rule: #8a8a8a;
    --emboss: #5c5c5c;
  }
  * { box-sizing: border-box; margin: 0; padding: 0; }
  html, body {
    width: 1200px; height: 801px; overflow: hidden;
    background: var(--stage);
    font-family: "Open Sans", Arial, sans-serif;
  }
  .sheet {
    width: 1200px; height: 801px;
    display: flex; align-items: center; justify-content: center; gap: 40px;
  }
  .card {
    width: 540px; height: 309px;
    background: var(--card);
    position: relative;
    box-shadow: 0 10px 30px rgba(0,0,0,.45);
  }
  .card--back { background: var(--card-back); }

  /* Front */
  .brand {
    position: absolute; left: 34px; top: 112px; width: 210px;
    text-align: center;
  }
  .brand__name {
    font-weight: 700; font-size: 26px; line-height: 1.15;
    letter-spacing: 1px; text-transform: uppercase; color: var(--ink);
  }
  .rule-pair {
    display: flex; align-items: center; justify-content: center; gap: 28px;
    margin-top: 12px;
  }
  .rule {
    width: 70px; height: 1px; background: var(--rule); position: relative;
  }
  .rule::before, .rule::after {
    content: ""; position: absolute; top: -1.5px; width: 4px; height: 4px;
    border-radius: 50%; background: var(--rule);
  }
  .rule::before { left: -2px; }
  .rule::after { right: -2px; }
  .divider {
    position: absolute; left: 266px; top: 66px; width: 1px; height: 138px;
    background: var(--rule);
  }
  .contact {
    position: absolute; left: 290px; top: 66px; color: var(--ink);
  }
  .contact__name {
    font-weight: 700; font-size: 18px; letter-spacing: 1px; text-transform: uppercase;
  }
  .contact__role { font-size: 13px; color: var(--ink-soft); margin-bottom: 10px; }
  .contact__line {
    display: flex; align-items: center; gap: 8px;
    font-size: 13px; color: var(--ink-soft); line-height: 22px;
  }
  .contact__line svg { width: 12px; height: 12px; flex: none; }
  .tagline {
    position: absolute; left: 290px; top: 232px;
    font-size: 13px; letter-spacing: .5px; text-transform: uppercase; color: var(--ink);
  }

  /* Back */
  .back-brand {
    position: absolute; left: 0; right: 0; top: 108px; text-align: center;
  }
  .back-brand__name {
    font-weight: 700; font-size: 34px; letter-spacing: 1.5px;
    text-transform: uppercase; color: var(--emboss);
  }
  .back-brand .rule-pair { gap: 40px; margin-top: 16px; }
  .back-brand .rule { width: 100px; background: var(--emboss); }
  .back-brand .rule::before, .back-brand .rule::after { background: var(--emboss); }
</style>
</head>
<body>
<main class="sheet">
  <section class="card card--front" aria-label="Business card front">
    <div class="brand">
      <p class="brand__name">Calden<br>Leafworks</p>
      <div class="rule-pair"><span class="rule"></span><span class="rule"></span></div>
    </div>
    <div class="divider"></div>
    <div class="contact">
      <p class="contact__name">Kevin Oldacre</p>
      <p class="contact__role">Owner</p>
      <p class="contact__line">
        <svg viewBox="0 0 12 12" aria-hidden="true"><circle cx="6" cy="6" r="6" fill="#fff"/><path d="M4 3.2l1 1.6-.6.7c.5 1 1.1 1.6 2.1 2.1l.7-.6 1.6 1-.5 1C6 9 3 6 3.2 3.7z" fill="#111"/></svg>
        555-017-4863
      </p>
      <p class="contact__line">
        <svg viewBox="0 0 12 12" aria-hidden="true"><circle cx="6" cy="6" r="6" fill="#fff"/><rect x="3" y="4" width="6" height="4.2" fill="none" stroke="#111" stroke-width=".9"/><path d="M3 4l3 2.3L9 4" fill="none" stroke="#111" stroke-width=".9"/></svg>
        koldacre@caldenleaf.com
      </p>
      <p class="contact__line">
        <svg viewBox="0 0 12 12" aria-hidden="true"><circle cx="6" cy="6" r="6" fill="#fff"/><circle cx="6" cy="6" r="3" fill="none" stroke="#111" stroke-width=".8"/><path d="M3 6h6M6 3c-1.4 1.6-1.4 4.4 0 6M6 3c1.4 1.6 1.4 4.4 0 6" fill="none" stroke="#111" stroke-width=".7"/></svg>
        caldenleafworks.com
      </p>
    </div>
    <p class="tagline">Savor every leaf</p>
  </section>

  <section class="card card--back" aria-label="Business card back">
    <div class="back-brand">
      <p class="back-brand__name">Calden Leafworks</p>
      <div class="rule-pair"><span class="rule"></span><span class="rule"></span></div>
    </div>
  </section>
</main>
</body>
</html>
```